Modern Business Card

Modern professional business card with more than just logo and demographic info. Something memorable.

We are a trendy/modern chiropractic group with an emphasis on neurology, hence the minimalist-type brain logo. We want to convey that modern and technical aspect with professionalism and the elite nature of our practice environment.

```html
<!DOCTYPE html>
<html lang="en">
<head>
<meta charset="utf-8">
<title>Meridian Chiropractic – Business Card</title>
<link href="https://fonts.googleapis.com/css2?family=Cormorant+Garamond:wght@600&family=Exo+2:wght@400&display=swap" rel="stylesheet">
<style>
  :root {
    --stage: #1c1c1e;
    --ink: #0a0b0d;
    --paper: #ffffff;
    --brand-blue: #4a82c8;
    --steel: #5b5c5e;
    --pattern-dark: #15161a;
    --pattern-light: #22242a;
  }
  * { box-sizing: border-box; margin: 0; padding: 0; }
  html, body { width: 1200px; height: 900px; overflow: hidden; }
  body {
    background: radial-gradient(ellipse at 50% 30%, #2b2b2e 0%, var(--stage) 70%);
    position: relative;
  }
  .card {
    position: absolute;
    left: 250px;
    width: 700px;
    height: 400px;
    overflow: hidden;
  }
  .card--back { top: 35px; background: var(--ink); }
  .card--front { top: 465px; background: var(--paper); }

  .back-texture {
    position: absolute; inset: 0;
    background: linear-gradient(135deg, var(--pattern-light) 0%, var(--pattern-dark) 50%, var(--pattern-light) 100%);
  }
  .back-brand {
    position: absolute; left: 0; right: 0; top: 140px;
    display: flex; flex-direction: column; align-items: center; gap: 40px;
  }
  .brand-dot {
    width: 48px; height: 48px; border-radius: 50%;
    background: var(--brand-blue);
  }
  .brand-name {
    font-family: "Cormorant Garamond", Georgia, serif;
    font-weight: 600;
    text-transform: uppercase;
    letter-spacing: 1px;
    line-height: 1;
  }
  .back-brand .brand-name { color: var(--paper); font-size: 28px; text-align: center; }

  .front-brand {
    position: absolute; left: 40px; top: 50px;
    display: flex; align-items: center; gap: 14px;
  }
  .front-brand .brand-dot { width: 44px; height: 44px; }
  .front-brand .brand-name { color: var(--ink); font-size: 32px; }

  .wave { position: absolute; inset: 0; }

  .contact {
    position: absolute; right: 30px; top: 272px;
    text-align: right; color: var(--paper);
    font-family: "Exo 2", Arial, sans-serif;
  }
  .contact__name {
    font-family: "Cormorant Garamond", Georgia, serif;
    font-weight: 600; font-size: 27px; letter-spacing: 1px;
    text-transform: uppercase; margin-right: 26px; line-height: 1;
  }
  .contact__role { color: var(--brand-blue); font-size: 17px; margin-right: 26px; margin-bottom: 8px; }
  .contact__line {
    display: flex; justify-content: flex-end; align-items: center; gap: 10px;
    font-size: 15px; line-height: 22px;
  }
  .contact__line .accent { color: var(--brand-blue); }
  .contact__icon { width: 16px; height: 16px; flex: none; }
</style>
</head>
<body>

<section class="card card--back">
  <div class="back-texture" role="img" aria-label="Dark repeating brand texture background"></div>
  <div class="back-brand">
    <span class="brand-dot"></span>
    <span class="brand-name">Meridian Chiropractic</span>
  </div>
</section>

<section class="card card--front">
  <svg class="wave" viewBox="0 0 700 400" width="700" height="400" aria-hidden="true">
    <path d="M0,190 C120,270 380,285 600,250 C380,272 130,262 0,215 Z" fill="var(--steel)"/>
    <path d="M360,232 C500,192 640,186 700,206 L700,222 C630,206 500,210 360,232 Z" fill="var(--brand-blue)"/>
    <path d="M0,232 C170,302 420,302 700,226 L700,400 L0,400 Z" fill="var(--ink)"/>
  </svg>

  <div class="front-brand">
    <span class="brand-dot"></span>
    <span class="brand-name">Meridian Chiropractic</span>
  </div>

  <div class="contact">
    <p class="contact__name">Daniel Carver</p>
    <p class="contact__role">Training Specialist</p>
    <p class="contact__line">555.014.2290
      <svg class="contact__icon" viewBox="0 0 16 16" aria-hidden="true"><circle cx="8" cy="8" r="7" fill="none" stroke="var(--brand-blue)" stroke-width="1.4"/><path d="M5.5,4.5 l1.5,0 l0.6,2 l-1,0.8 a5,5 0 0 0 2.2,2.2 l0.8,-1 l2,0.6 l0,1.5 a1,1 0 0 1 -1,1 a6,6 0 0 1 -6,-6 a1,1 0 0 1 1,-1 z" fill="var(--brand-blue)"/></svg>
    </p>
    <p class="contact__line">d.carver@meridianchiro.com
      <svg class="contact__icon" viewBox="0 0 16 16" aria-hidden="true"><rect x="1.5" y="3.5" width="13" height="9" fill="none" stroke="var(--brand-blue)" stroke-width="1.4"/><path d="M1.5,3.5 L8,9 L14.5,3.5" fill="none" stroke="var(--brand-blue)" stroke-width="1.4"/></svg>
    </p>
    <p class="contact__line">www.<span class="accent">meridianchiro</span>.com
      <svg class="contact__icon" viewBox="0 0 16 16" aria-hidden="true"><circle cx="8" cy="8" r="6.5" fill="none" stroke="var(--brand-blue)" stroke-width="1.4"/><ellipse cx="8" cy="8" rx="3" ry="6.5" fill="none" stroke="var(--brand-blue)" stroke-width="1.2"/><path d="M1.5,8 H14.5" stroke="var(--brand-blue)" stroke-width="1.2"/></svg>
    </p>
  </div>
</section>

</body>
</html>
```